Business Cards for IT Consulting Company (Managed Service Provider)

I am looking to have some business cards printed and would like some designs. We are an IT Consulting company based in Vancouver BC. I would like a nice clean and modern look to the cards. I have uploaded all the versions of my logo so parts can be used as needed. Here is a snippit from our website homepage:

Quillbrook Networks Ltd. is an IT Solutions Partner located in Vancouver BC, Canada. We offer IT solutions and support to customers in the greater Vancouver Area. With expertise in Microsoft platforms, as well as Linux and Mac OSX and over 12 years experience in the IT industry, Quillbrook Networks is dedicated to offering our clients top quality service and products. We take pride in the solutions we offer our customers. The greatest compliment a client can give us is to recommend our services.

Quillbrook Networks Ltd. offers a wide range of IT services from onsite service to remote support and managed service solutions. This allows clients to choose the support path that best suits their company’s needs. Supporting many different sized companies from small to enterprise level over the past 12 years Quillbrook Networks has the experience and expertise needed to ensure things run smoothly. Allowing our clients to focus on doing business.

Revolutionizing the way IT services are delivered.

Quillbrook Networks is dedicated to providing our clients with IT solutions that work and grow with them for years to come. This philosophy helps save money in the long run instead of replacing equipment constantly. Far too often IT solutions are not well thought out and while possibly solving the problem at hand, require replacement due to growth or quality within a very short time frame. Quillbrook Networks takes pride in providing solutions that will last and be able to accommodate growth without the need for replacement.

Industry/Entity Type

Information Technology

Contact Information for Business Card

Quillbrook Networks Ltd.
(Employee Name)
Eml: (Employees Email Address)
Web: quillbrook.me
Ph: 604-555-0148

Font styles to use
Serif
Sans Serif

Requirements
Must have
• The Company logo and company colors.
Nice to have
• - Our tag line: "Revolutionizing IT Services" or "Revolutionizing the way IT services are delivered."
• - Also I really like the idea of nature and technology together blending which is sort of where my logo came from so integrating that somehow onto the business cards would be great.

```html
<!DOCTYPE html>
<html lang="en">
<head>
<meta charset="utf-8">
<title>Quillbrook Networks Ltd. — Business Cards</title>
<link rel="stylesheet" href="https://fonts.googleapis.com/css2?family=Raleway:wght@400;500;600&display=swap">
<style>
  :root {
    --backdrop: #cfe8df;
    --card: #ffffff;
    --brand-blue: #1a97d9;
    --brand-blue-soft: #d7ecf8;
    --ink: #2b2b2b;
    --shadow: rgba(40, 80, 70, 0.18);
  }
  * { box-sizing: border-box; margin: 0; padding: 0; }
  html, body { width: 1200px; height: 856px; overflow: hidden; }
  body {
    background: var(--backdrop);
    font-family: "Raleway", Arial, sans-serif;
    position: relative;
  }
  .card {
    position: absolute;
    width: 540px;
    height: 308px;
    background: var(--card);
    border-radius: 26px;
    box-shadow: 0 10px 28px var(--shadow);
    overflow: hidden;
  }
  .card--back { left: 600px; top: 110px; }
  .card--front { left: 70px; top: 440px; }

  .wordmark {
    display: flex;
    align-items: center;
    gap: 14px;
    color: var(--brand-blue);
    font-weight: 600;
  }
  .wordmark__square {
    width: 38px; height: 38px;
    background: var(--brand-blue);
    border-radius: 4px;
    flex: none;
  }
  .wordmark__name { font-size: 30px; line-height: 1.1; letter-spacing: 0.2px; }

  .card--back .wordmark { position: absolute; left: 60px; top: 78px; }
  .tagline {
    position: absolute;
    left: 0; right: 0; top: 196px;
    text-align: center;
    font-size: 26px;
    font-weight: 400;
    color: var(--ink);
  }
  .tagline__lead { color: var(--brand-blue); }

  .brand-graphic {
    position: absolute;
    left: 0; top: 0; bottom: 0;
    width: 200px;
    background: linear-gradient(135deg, var(--brand-blue-soft), #bfe0f4);
  }
  .card--front .wordmark {
    position: absolute; left: 228px; top: 32px;
  }
  .card--front .wordmark__square { width: 24px; height: 24px; }
  .card--front .wordmark__name { font-size: 19px; }

  .person {
    position: absolute; left: 228px; top: 104px;
    font-size: 28px; font-weight: 400;
    color: var(--brand-blue);
    letter-spacing: 1px;
    text-transform: uppercase;
  }
  .contact-list {
    position: absolute; left: 228px; top: 162px;
    list-style: none;
    display: flex; flex-direction: column; gap: 12px;
  }
  .contact-list__item {
    display: flex; align-items: center; gap: 12px;
    font-size: 17px; color: var(--ink); font-weight: 500;
  }
  .contact-list__icon {
    width: 28px; height: 28px; flex: none;
    border-radius: 50%;
    background: var(--brand-blue);
    display: flex; align-items: center; justify-content: center;
  }
</style>
</head>
<body>

  <section class="card card--back" aria-label="Business card back">
    <div class="wordmark">
      <span class="wordmark__square"></span>
      <span class="wordmark__name">Quillbrook Networks Ltd.</span>
    </div>
    <p class="tagline"><span class="tagline__lead">Revolutionizing</span> IT Services</p>
  </section>

  <section class="card card--front" aria-label="Business card front">
    <div class="brand-graphic" role="img" aria-label="Large decorative brand graphic in blue"></div>
    <div class="wordmark">
      <span class="wordmark__square"></span>
      <span class="wordmark__name">Quillbrook Networks Ltd.</span>
    </div>
    <p class="person">Dana Whitfield</p>
    <ul class="contact-list">
      <li class="contact-list__item">
        <span class="contact-list__icon">
          <svg width="16" height="16" viewBox="0 0 16 16" aria-hidden="true"><rect x="2" y="4" width="12" height="8" rx="1" fill="none" stroke="#fff" stroke-width="1.4"/><path d="M2 4l6 5 6-5" fill="none" stroke="#fff" stroke-width="1.4"/></svg>
        </span>
        dana.whitfield@quillbrook.me
      </li>
      <li class="contact-list__item">
        <span class="contact-list__icon">
          <svg width="16" height="16" viewBox="0 0 16 16" aria-hidden="true"><circle cx="8" cy="8" r="6" fill="none" stroke="#fff" stroke-width="1.3"/><ellipse cx="8" cy="8" rx="2.6" ry="6" fill="none" stroke="#fff" stroke-width="1.1"/><path d="M2 8h12M3 5h10M3 11h10" stroke="#fff" stroke-width="1"/></svg>
        </span>
        quillbrook.me
      </li>
      <li class="contact-list__item">
        <span class="contact-list__icon">
          <svg width="16" height="16" viewBox="0 0 16 16" aria-hidden="true"><path d="M4.5 2.5l2 2.6-1.2 1.5c.8 1.7 2 2.9 3.7 3.7l1.5-1.2 2.6 2-1.2 2c-5-.4-8.9-4.3-9.3-9.3z" fill="#fff"/></svg>
        </span>
        604-555-0148
      </li>
    </ul>
  </section>

</body>
</html>
```